Tessel - Web Design Project

We are seeking to have our website redesigned. Our current webpage is rather dated looking www.tessel-momentum.example We will be utilizing similar content to explain our services as what is in the website now. We do not see it at a retail portal but rather a website for those inquiring about our services as a reference check so to speak.

We wish to have a look that is considered clean, fresh, contemporary and contains a business savvy vibe.

We prefer isolated white background and also wish to retain the integrity of our Logo and colour scheme.

We are looking for something that doesnt look like it was designed at home on sitenook. We are hoping to find something that looks like it would reside on a tablet.

Hello designers!

We apologize for our tardiness as we have been quite preoccupied. We will be extending our invites to the end of January!

Hello All,

Please review our offer once again for updated requirements.  We are hoping to accept a design by months end.

Tessel

Target Market(s)

Business to business clients and Large manufacturers

Industry/Entity Type

Retail

Requirements
Must have
• Existing Logo

There must be an area dedicated to an intro video that will be incorporated on our landing page.

We require design of the other pages as well not only the landing page.

```html
<!DOCTYPE html>
<html lang="en">
<head>
<meta charset="utf-8">
<title>Tessel Performance Group</title>
<link rel="stylesheet" href="https://fonts.googleapis.com/css2?family=Arimo:ital,wght@0,400;0,700;1,400&display=swap">
<style>
:root{
  --red:#e3141a;
  --deep-red:#7e1416;
  --slate:#555050;
  --text:#5f5f5f;
  --rule:#d8d8d8;
  --footer:#dde0e6;
  --video:#000516;
}
*{box-sizing:border-box;margin:0;padding:0}
html,body{width:1200px;height:1000px;overflow:hidden;background:#fff}
body{position:relative;font-family:"Arimo",Arial,sans-serif;color:var(--text)}
.top-strip{position:absolute;top:0;left:0;width:1200px;height:9px;background:#5a5a5a}
.top-strip::after{content:"";position:absolute;left:120px;width:960px;height:9px;background:var(--red)}
.brand{position:absolute;left:119px;top:38px;display:flex;align-items:center;gap:8px;font-size:48px;color:#555;letter-spacing:-1px}
.brand-dot{width:14px;height:14px;border-radius:50%;background:var(--red)}
.main-nav{position:absolute;top:58px;right:121px;display:flex;gap:32px;font-size:16px;color:#555}
.rule{position:absolute;left:120px;width:960px;height:1px;background:var(--rule)}
.search{position:absolute;left:119px;top:135px;display:flex;align-items:center;font-size:18px;color:#555}
.search-field{width:220px;height:26px;border:1px solid #ccc;margin-left:12px}
.search-go{width:26px;height:26px;background:#555;margin-left:5px;color:#fff;font-size:14px;display:flex;align-items:center;justify-content:center;font-weight:700}
.account{position:absolute;right:120px;top:137px;display:flex;align-items:center;gap:16px;font-size:15px;color:var(--red)}
.account .sep{width:1px;height:18px;background:var(--rule)}
.flags{display:flex;gap:10px}
.stage-bg{position:absolute;top:172px;left:0;width:1200px;height:258px;background:linear-gradient(#fff,#ccd1d9)}
.stage-shadow{position:absolute;top:430px;left:40px;width:1120px;height:110px;background:radial-gradient(ellipse at 50% 0,#cfc9c4 0,#fff 70%)}
.hero{position:absolute;left:120px;top:172px;width:960px;height:360px;background:linear-gradient(160deg,#5b97d6 0%,#a7cdee 45%,#7aa8d8 100%)}
.hero-photo{position:absolute;inset:0;background:linear-gradient(100deg,transparent 45%,rgba(90,95,110,.55) 55%,rgba(200,205,215,.5) 66%,transparent 72%)}
.hero-base{position:absolute;left:120px;top:532px;width:960px;height:9px;background:#555}
.video{position:absolute;left:33px;top:34px;width:501px;height:302px;background:var(--video)}
.video-controls{position:absolute;left:0;bottom:0;width:100%;height:19px;background:linear-gradient(#f2f2f2,#c9c9c9);font-size:9px;color:#222}
.quote{position:absolute;left:658px;top:115px;width:302px;height:154px;background:rgba(160,200,235,.55);padding:24px 22px 0 10px;text-align:right;font-size:16px;line-height:23px;font-style:italic;color:#2c3a4a}
.quote span{font-style:normal}
.tagline{position:absolute;left:100px;top:577px;width:1000px;text-align:center;font-size:20px;line-height:28px;color:#666}
.intro{position:absolute;left:119px;top:700px;width:630px;font-size:15px;line-height:24px}
.cta{position:absolute;left:780px;width:300px;height:50px;display:flex;align-items:center;color:#fff;font-size:21px}
.cta-arrow{width:40px;height:50px;background:var(--red);display:flex;align-items:center;justify-content:center;font-weight:700;font-size:16px;margin-right:14px}
.cta b{margin-right:6px}
.cta-performance{top:703px;background:var(--deep-red)}
.cta-sustain{top:768px;background:var(--slate)}
.closing{position:absolute;left:119px;top:887px;font-size:15px}
.closing a{color:var(--red);text-decoration:none}
.site-footer{position:absolute;top:940px;left:0;width:1200px;height:60px;background:var(--footer);font-size:13px;color:#666}
.contact{position:absolute;left:117px;top:32px;line-height:18px}
.follow{position:absolute;right:120px;top:38px;display:flex;align-items:center;gap:8px}
.follow i{width:24px;height:24px;background:#666;display:block}
.follow .label{margin-right:6px}
</style>
</head>
<body>
<div class="top-strip"></div>
<div class="brand"><span class="brand-dot"></span>tessel</div>
<nav class="main-nav"><span>Home</span><span>Who we are</span><span>Cross the Tessel</span><span>Performance Solutions</span><span>Sustain Solutions</span></nav>
<div class="rule" style="top:120px"></div>
<div class="search">Search<span class="search-field"></span><span class="search-go">›</span></div>
<div class="account">Sign In<span class="sep"></span>
  <span class="flags">
    <svg width="22" height="15" viewBox="0 0 22 15"><rect width="22" height="15" fill="#1f3f8a"/><rect x="9" width="4" height="15" fill="#fff"/><rect y="5.5" width="22" height="4" fill="#fff"/><rect x="10" width="2" height="15" fill="#c8102e"/><rect y="6.5" width="22" height="2" fill="#c8102e"/></svg>
    <svg width="22" height="15" viewBox="0 0 22 15"><rect width="7.3" height="15" fill="#1f3f9a"/><rect x="7.3" width="7.4" height="15" fill="#fff"/><rect x="14.7" width="7.3" height="15" fill="#e3141a"/></svg>
  </span>
</div>
<div class="stage-bg"></div>
<div class="stage-shadow"></div>
<section class="hero">
  <div class="hero-photo" role="img" aria-label="Photograph of a curved concrete highway overpass against a blue sky with clouds"></div>
  <div class="video">
    <svg style="position:absolute;left:217px;top:109px" width="70" height="70" viewBox="0 0 70 70"><circle cx="35" cy="35" r="33" fill="none" stroke="#fff" stroke-width="3"/><path d="M28 21 L49 35 L28 49 Z" fill="#fff"/></svg>
    <div class="video-controls">
      <svg style="position:absolute;left:10px;top:5px" width="10" height="10"><path d="M1 0 L10 5 L1 10Z" fill="#222"/></svg>
      <div style="position:absolute;left:38px;top:8px;width:360px;height:3px;background:#999"></div>
      <div style="position:absolute;left:47px;top:4px;width:8px;height:11px;background:#444;border-radius:2px"></div>
      <span style="position:absolute;left:405px;top:4px">0:04 / 2:32</span>
    </div>
  </div>
  <blockquote class="quote">“There are managers so preoccupied with their e-mail messages that they never look up from their screens to see what’s happening in the nondigital world.” <span>Anselm Varga</span></blockquote>
</section>
<div class="hero-base"></div>
<p class="tagline">Tessel Performance Group Inc. are highly experienced performance consultants, trainers and subject matter experts based throughout the North America, Europe, the Middle East and Asia Pacific</p>
<div class="rule" style="top:665px"></div>
<p class="intro">Tessel Performance Group Inc. is the leading provider of profit generating and people development solutions. With the hands-on experience of best practices, the state-of-the-art technology and in-depth information we help companies increase their efficiencies and profits. Frank, honest, committed, valuable and rewarding are words that customers use to describe the quality services provided by Tessel Performance Group.</p>
<div class="cta cta-performance"><span class="cta-arrow">›</span><b>Performance</b>Solutions</div>
<div class="cta cta-sustain"><span class="cta-arrow">›</span><b>Sustain</b>Solutions</div>
<div class="rule" style="top:855px"></div>
<p class="closing"><a href="#">Learn more about us</a>, or find the right <a href="#">solutions</a> for your specific business. We will be delighted to help you achieve better business results.</p>
<footer class="site-footer">
  <div class="contact"><b>Tessel Performance Group .</b> 820 Harbourview Rd . Lunenfield . NS B0J 2K7 . Canada<br><b>Telephone :</b>+1 888 555 0142 &nbsp;<b>Email:</b>info@tessel-momentum.example</div>
  <div class="follow"><span class="label">Follow us on</span><i></i><i></i><i></i></div>
</footer>
</body>
</html>
```